Pinecrest Capital Group - Company Envelopes

I am looking for a graphic designer to create a bespoke envelope for my company use, which I can then have printed at scale. The envelope should be of standard size and shape, but Matt black in colour, with semi-thick vertical gloss (shiny) lines going from left to right, but must stop to the right of the envelope, leaving a Matt black line with enough space for a stamp in the top right corner. The back of the envelope should be full Matt black.

Requirements
Must have
• Must be as described in brief
Should not have
• No other colours - Just Matt and Gloss Black

```html
<!DOCTYPE html>
<html lang="en">
<head>
<meta charset="utf-8">
<title>Pinecrest Capital Group – Company Envelopes</title>
<link rel="stylesheet" href="https://fonts.googleapis.com/css2?family=Cinzel:wght@600&display=swap">
<style>
  :root {
    --backdrop: #5e5e5e;
    --matt-black: #0c0c0c;
    --gloss-black: #000000;
    --stamp-field: #1b1b1b;
    --gloss-light: #bdbdbd;
    --edge-line: #d8d8d8;
    --seam-line: #2a2a2a;
    --ink-white: #f2f2f2;
  }
  html, body {
    margin: 0;
    padding: 0;
    overflow: hidden;
  }
  .canvas {
    position: relative;
    width: 1200px;
    height: 895px;
    background: var(--backdrop);
    overflow: hidden;
  }
  .envelope {
    position: absolute;
    left: 364.5px;
    width: 471px;
    height: 332.5px;
    display: block;
  }
  .envelope--back { top: 92.6px; }
  .envelope--front { top: 469.5px; }
  .company-name {
    font-family: "Cinzel", "Times New Roman", serif;
    font-weight: 600;
    fill: var(--ink-white);
  }
</style>
</head>
<body>
<div class="canvas">

  <!-- Back of envelope: full matt black with flap -->
  <svg class="envelope envelope--back" viewBox="673 171 870 614" aria-label="Envelope back, matt black">
    <rect class="paper" x="673" y="171" width="870" height="614" fill="var(--matt-black)"/>
    <path class="flap" d="M673 171 L705 280 Q718 309 745 309 L1473 309 Q1502 309 1515 280 L1543 171 Z"
          fill="var(--gloss-black)" stroke="var(--edge-line)" stroke-width="1.2"/>
  </svg>

  <!-- Front of envelope: matt black with gloss stripes and stamp area -->
  <svg class="envelope envelope--front" viewBox="673 867 870 614" aria-label="Envelope front with gloss stripes">
    <defs>
      <linearGradient id="glossFade" x1="0" y1="0" x2="0" y2="1" gradientUnits="userSpaceOnUse"
                      gradientTransform="translate(0 867) scale(1 614)">
        <stop offset="0.30" stop-color="#000000"/>
        <stop offset="0.55" stop-color="#7a7a7a"/>
        <stop offset="0.75" stop-color="var(--gloss-light)"/>
        <stop offset="1" stop-color="var(--gloss-light)"/>
      </linearGradient>
    </defs>

    <rect class="paper" x="673" y="867" width="870" height="614" fill="var(--matt-black)"/>

    <!-- Short gloss stripes, upper left -->
    <g class="gloss-stripes gloss-stripes--short" fill="var(--gloss-black)" stroke="var(--seam-line)" stroke-width="1">
      <rect x="673" y="867" width="59" height="338"/>
      <rect x="755" y="867" width="58" height="338"/>
      <rect x="836" y="867" width="58" height="338"/>
      <rect x="917" y="867" width="58" height="338"/>
    </g>

    <!-- Full-height gloss stripes, centre -->
    <g class="gloss-stripes gloss-stripes--full" fill="url(#glossFade)">
      <rect x="998" y="867" width="59" height="614"/>
      <rect x="1079" y="867" width="58" height="614"/>
      <rect x="1160" y="867" width="59" height="614"/>
    </g>

    <!-- Stamp area -->
    <rect class="stamp-field" x="1260" y="927" width="233" height="233" fill="var(--stamp-field)"/>

    <!-- Gloss stripes below stamp -->
    <g class="gloss-stripes gloss-stripes--lower" fill="var(--gloss-light)">
      <rect x="1241" y="1164" width="59" height="317"/>
      <rect x="1322" y="1164" width="59" height="317"/>
      <rect x="1404" y="1164" width="58" height="317"/>
      <rect x="1485" y="1164" width="58" height="317"/>
    </g>

    <!-- Company name -->
    <g class="brand">
      <text class="company-name" x="705" y="1275" font-size="38" textLength="268" lengthAdjust="spacingAndGlyphs">PINECREST</text>
      <text class="company-name" x="705" y="1300" font-size="16" textLength="268" lengthAdjust="spacing">CAPITAL GROUP</text>
    </g>
  </svg>

</div>
</body>
</html>
```